IT Company requires new Business Card design.

Over the years we have had a few different business card designs. We are now due for new cards across the board for all staff. We felt this would be a good time to start fresh with a new design. Our traditional card simply had our details on the front, and a list of services on the back. We don't particularly need the list of services, we have had cards where the only thing on the rear of the card was our logo.
Feel free to be creative, we would like our tag line "Complete IT Management" to appear at some point, doesn't necessarily have to be with the logo.
I have attached samples and drafts of various previous cards we have used over the years.

```html
<!DOCTYPE html>
<html lang="en">
<head>
<meta charset="utf-8">
<title>Bayline Networking – Business Card</title>
<link href="https://fonts.googleapis.com/css2?family=Open+Sans:wght@400;600;700&display=swap" rel="stylesheet">
<style>
  :root {
    --page: #e9e7e4;
    --metal-light: #fbfbfb;
    --metal-mid: #ececec;
    --metal-dark: #d2d3d4;
    --slate: #5b6870;
    --slate-dark: #4e5a61;
    --slate-light: #76838a;
    --ink: #3f4a50;
    --white: #ffffff;
  }
  * { box-sizing: border-box; margin: 0; padding: 0; }
  html, body {
    width: 1034px; height: 1200px; overflow: hidden;
    background: var(--page);
    font-family: "Open Sans", Arial, sans-serif;
  }
  .card {
    position: absolute; left: 67px; width: 900px; height: 518px;
    background: linear-gradient(160deg, var(--metal-mid) 0%, var(--metal-light) 45%, var(--metal-mid) 70%, var(--metal-dark) 100%);
    box-shadow: 0 4px 14px rgba(0,0,0,0.18);
    overflow: hidden;
  }
  .card--front { top: 62px; }
  .card--back { top: 620px; }

  .brand {
    position: absolute; left: 50px; top: 168px; width: 380px;
    display: flex; align-items: center; gap: 18px;
  }
  .brand__square { width: 56px; height: 56px; background: var(--slate); flex: none; }
  .brand__name {
    color: var(--slate); font-weight: 700; font-size: 38px; line-height: 1.05;
    letter-spacing: 0.5px; text-transform: uppercase;
  }

  .divider {
    position: absolute; left: 459px; top: 62px; width: 2px; height: 360px;
    background: linear-gradient(to bottom, rgba(91,104,112,0), rgba(91,104,112,0.35) 20%, rgba(91,104,112,0.35) 80%, rgba(91,104,112,0));
  }

  .details { position: absolute; left: 485px; top: 60px; color: var(--ink); }
  .details__name { font-size: 27px; font-weight: 700; color: var(--slate); line-height: 1.2; }
  .details__role { font-size: 21px; color: var(--slate-dark); margin-top: 2px; }
  .contact-list { list-style: none; margin-top: 26px; }
  .contact-list li {
    display: flex; align-items: center; gap: 12px;
    font-size: 20px; height: 34px; color: var(--ink);
  }
  .contact-list svg { width: 20px; height: 20px; flex: none; }
  .address { margin-top: 22px; font-size: 20px; line-height: 1.45; color: var(--ink); }

  .tag-band { position: absolute; left: 0; bottom: 0; width: 900px; height: 42px; }
  .tag-band svg { position: absolute; inset: 0; }
  .tag-band__text {
    position: absolute; right: 76px; top: 0; line-height: 42px;
    color: var(--white); font-size: 20px;
  }

  .back-brand {
    position: absolute; left: 0; top: 150px; width: 900px; text-align: center;
    color: var(--slate); font-weight: 700; font-size: 72px; line-height: 1.1;
    text-transform: uppercase; letter-spacing: 1px;
  }
  .back-url {
    position: absolute; left: 0; top: 462px; width: 900px; text-align: center;
    color: var(--ink); font-size: 25px; letter-spacing: 2.5px;
  }
  .back-url strong { color: var(--slate); font-weight: 700; }
</style>
</head>
<body>

<section class="card card--front">
  <div class="brand">
    <div class="brand__square"></div>
    <div class="brand__name">Bayline<br>Networking</div>
  </div>

  <div class="divider"></div>

  <div class="details">
    <div class="details__name">Marcus Reid</div>
    <div class="details__role">Operation Manager</div>
    <ul class="contact-list">
      <li>
        <svg viewBox="0 0 20 20" aria-hidden="true"><circle cx="10" cy="10" r="9" fill="none" stroke="#5b6870" stroke-width="1.5"/><path d="M6.5 5.5c.6-.6 1.4-.5 1.8.1l.8 1.3c.3.5.2 1-.2 1.4l-.5.5c.6 1.3 1.5 2.2 2.8 2.8l.5-.5c.4-.4.9-.5 1.4-.2l1.3.8c.6.4.7 1.2.1 1.8-1 1-2.4 1.1-3.6.4-1.9-1-3.5-2.6-4.5-4.5-.7-1.2-.6-2.6.1-3.9z" fill="#5b6870"/></svg>
        08 9000 1234
      </li>
      <li>
        <svg viewBox="0 0 20 20" aria-hidden="true"><rect x="6" y="2" width="8" height="16" rx="1.5" fill="#5b6870"/><rect x="7.3" y="4" width="5.4" height="7" fill="#ececec"/><circle cx="10" cy="15" r="1" fill="#ececec"/></svg>
        0400 123 456
      </li>
      <li>
        <svg viewBox="0 0 20 20" aria-hidden="true"><rect x="6" y="3" width="8" height="5" fill="#5b6870"/><rect x="2" y="8" width="16" height="8" rx="1.5" fill="#5b6870"/><rect x="5" y="12" width="10" height="2" fill="#ececec"/></svg>
        08 9000 1235
      </li>
      <li>
        <svg viewBox="0 0 20 20" aria-hidden="true"><circle cx="10" cy="10" r="9" fill="#5b6870"/><rect x="5" y="6.5" width="10" height="7" fill="#ececec"/><path d="M5 6.5l5 4 5-4" fill="none" stroke="#5b6870" stroke-width="1.2"/></svg>
        marcus@baylinenet.com.au
      </li>
      <li>
        <svg viewBox="0 0 20 20" aria-hidden="true"><circle cx="10" cy="10" r="8.5" fill="none" stroke="#5b6870" stroke-width="1.5"/><ellipse cx="10" cy="10" rx="3.5" ry="8.5" fill="none" stroke="#5b6870" stroke-width="1.2"/><path d="M2 10h16M3.5 6h13M3.5 14h13" stroke="#5b6870" stroke-width="1.2"/></svg>
        www.baylinenet.com.au
      </li>
    </ul>
    <p class="address">Unit 4 22 Harbour Way<br>Lakeview WA 6000</p>
  </div>

  <div class="tag-band">
    <svg viewBox="0 0 900 42" width="900" height="42" aria-hidden="true">
      <polygon points="0,0 470,0 440,42 0,42" fill="#76838a"/>
      <polygon points="478,0 900,0 900,42 448,42" fill="#4e5a61"/>
      <polygon points="470,0 478,0 448,42 440,42" fill="#f2f2f2"/>
    </svg>
    <span class="tag-band__text">Complete IT Management</span>
  </div>
</section>

<section class="card card--back">
  <div class="back-brand">Bayline<br>Networking</div>
  <p class="back-url">www.<strong>baylinenet</strong>.com.au</p>
</section>

</body>
</html>
```